Business Card for a mobile physiotherapy company

I need a layout for a business card for a mobile physiotherapy company.
Slogan is "Mobile Physiotherapy - Your Road To Recovery"
Phone number is 867-555-0142
Email VardenTherapy@postnest.ca (subject to change with website)
Website www.VardenTherapy.ca
My name and credentials: Luke Varden Luke Varden, BSc(kin), MPT, CAFCI, IMS
Information maybe included: Direct Billing, Services including Physiotherapy, IMS, acupuncture
Maybe include facebook and instagram logos
One side with the logo clean and sharp
Other side with details, try not to look too busy, keep everything concise

```html
<!DOCTYPE html>
<html lang="en">
<head>
<meta charset="utf-8">
<title>Varden Therapy – Business Card</title>
<link rel="stylesheet" href="https://fonts.googleapis.com/css2?family=Roboto:ital,wght@0,400;0,500;0,700;1,400&display=swap">
<style>
  :root {
    --navy: #2c4a72;
    --green: #0d5140;
    --ink: #4a4a4a;
    --rule: #6f6f6f;
    --card-white: #fafafa;
    --backdrop: #e4e4e4;
    --white: #ffffff;
  }
  * { box-sizing: border-box; margin: 0; padding: 0; }
  html, body {
    width: 1125px; height: 1200px; overflow: hidden;
    background: var(--backdrop);
    font-family: "Roboto", Arial, sans-serif;
  }
  .card {
    position: absolute; left: 171px; width: 826px; height: 472px;
    overflow: hidden;
    box-shadow: 0 2px 5px rgba(0,0,0,0.25);
  }
  .card--front { top: 106px; background: var(--card-white); }
  .card--back { top: 639px; background: var(--navy); }

  .brand-name {
    position: absolute; right: 62px; top: 178px;
    font-weight: 700; font-size: 34px; letter-spacing: 4px;
    color: var(--navy); white-space: nowrap;
  }
  .identity { position: absolute; left: 42px; top: 228px; }
  .identity__name { font-weight: 500; font-size: 29px; color: var(--navy); line-height: 1.05; text-transform: uppercase; }
  .identity__credentials { font-size: 19px; color: var(--navy); margin-top: 1px; }
  .identity__billing { font-size: 20px; color: var(--green); margin-top: 4px; font-weight: 500; }
  .divider { position: absolute; left: 42px; top: 323px; width: 723px; height: 1.5px; background: var(--rule); }

  .contact { position: absolute; left: 42px; top: 340px; list-style: none; }
  .contact li { display: flex; align-items: center; font-size: 19px; color: var(--ink); height: 26.5px; }
  .contact svg { width: 18px; height: 18px; margin-right: 12px; fill: var(--navy); }

  .bands { position: absolute; left: 0; bottom: 0; }
  .slogan {
    position: absolute; right: 26px; bottom: 11px;
    font-style: italic; font-size: 19.5px; color: var(--white);
  }

  .social { position: absolute; right: 50px; top: 44px; display: flex; gap: 5px; }
  .social span { width: 38px; height: 38px; border-radius: 50%; background: var(--white); }

  .brand-name--back {
    position: absolute; left: 0; right: 0; top: 180px; text-align: center;
    font-weight: 700; font-size: 52px; letter-spacing: 6px; color: var(--white);
  }
  .services {
    position: absolute; left: 0; right: 0; top: 392px;
    display: flex; justify-content: center; align-items: center;
    font-size: 19.5px; color: var(--white);
  }
  .services::before, .services::after {
    content: ""; width: 82px; height: 1px; margin: 0 2px;
  }
  .services::before { background: linear-gradient(90deg, transparent, var(--white)); }
  .services::after { background: linear-gradient(90deg, var(--white), transparent); }
</style>
</head>
<body>
  <section class="card card--front">
    <div class="brand-name">VARDEN THERAPY</div>

    <div class="identity">
      <h1 class="identity__name">Luke Varden</h1>
      <p class="identity__credentials">BSc(kin), MPT, CAFCI, IMS</p>
      <p class="identity__billing">Direct Billing</p>
    </div>
    <div class="divider"></div>

    <ul class="contact">
      <li><svg viewBox="0 0 24 24"><path d="M6.6 10.8a15.1 15.1 0 0 0 6.6 6.6l2.2-2.2c.3-.3.7-.4 1-.2 1.1.4 2.3.6 3.6.6.6 0 1 .4 1 1V20c0 .6-.4 1-1 1A17 17 0 0 1 3 4c0-.6.4-1 1-1h3.5c.6 0 1 .4 1 1 0 1.3.2 2.5.6 3.6.1.3 0 .7-.2 1z"/></svg>867-555-0142</li>
      <li><svg viewBox="0 0 24 24"><path d="M2 5h20v14H2zm2 2v.5l8 5 8-5V7zm0 3v7h16v-7l-8 5z"/></svg>VardenTherapy@postnest.ca</li>
      <li><svg viewBox="0 0 24 24"><circle cx="12" cy="12" r="10"/></svg>www.VardenTherapy.ca</li>
    </ul>

    <svg class="bands" width="826" height="46" viewBox="0 0 826 46">
      <polygon points="0,29 345,29 331,46 0,46" fill="var(--green)"/>
      <polygon points="380,0 826,0 826,46 336,46" fill="var(--navy)"/>
    </svg>
    <p class="slogan">Mobile Physiotherapy - Your Road To Recovery</p>
  </section>

  <section class="card card--back">
    <div class="social"><span></span><span></span></div>
    <div class="brand-name--back">VARDEN THERAPY</div>
    <p class="services">Physiotherapy • IMS • Acupuncture</p>
  </section>
</body>
</html>
```